Kettleby Twins Playing Cards

We are wanting a cool design for a playing card that includes our logo(s). I will attach our two logos, we are open to using either one of them or another version of them. I will also attach some pictures of card decks to use for inspiration. These are just decks that we have seen from other artists that we liked. We are located in West Texas so although not necessary, a Sotol or Agave or cactus or quail (bird) or some sort of sunset would pay homage to our surroundings. I realize the examples are all very different, but those are just some decks that we like! Thank you!

```html
<!DOCTYPE html>
<html lang="en">
<head>
<meta charset="utf-8">
<title>Kettleby Twins Playing Cards – Deck Layout</title>
<link href="https://fonts.googleapis.com/css2?family=Roboto+Slab:wght@700&display=swap" rel="stylesheet">
<style>
:root{
  --page:#ffffff;
  --card:#050607;
  --card-edge:#3b3a35;
  --card-line:#1c1c1a;
  --red:#d3202e;
  --silver:#c8c2b2;
  --back-blue:#1f73c9;
  --back-deep:#0d4f9c;
}
*{box-sizing:border-box;margin:0;padding:0}
html,body{width:1200px;height:546px;overflow:hidden;background:var(--page)}
.sheet{position:relative;width:1200px;height:546px}
.suit-row{position:absolute;left:33px;display:flex;gap:11.5px}
.row-hearts{top:26px}
.row-spades{top:139px}
.row-diamonds{top:304px}
.row-clubs{top:418px}
.card{position:relative;width:70px;height:97px;background:var(--card);border:1.5px solid var(--card-edge);border-radius:2px;box-shadow:inset 0 0 0 2px var(--card-line);overflow:hidden}
.red{color:var(--red)}
.silver{color:var(--silver)}
.idx{position:absolute;left:4px;top:3px;display:flex;flex-direction:column;align-items:center;font-family:"Roboto Slab",serif;font-weight:700;font-size:9px;line-height:1;letter-spacing:-.5px}
.idx svg{width:6px;height:6px;fill:currentColor;margin-top:1px}
.idx-b{left:auto;top:auto;right:4px;bottom:3px;transform:rotate(180deg)}
.pip{position:absolute;width:11px;height:11px;fill:currentColor;transform:translate(-50%,-50%)}
.x-l{left:33%}.x-c{left:50%}.x-r{left:67%}
.y-a{top:17%}.y-b{top:39%}.y-m{top:50%}.y-c{top:61%}.y-d{top:83%}.y-e{top:28%}.y-f{top:72%}
.y-c,.y-d,.y-f{transform:translate(-50%,-50%) rotate(180deg)}
.art{position:absolute;left:14px;right:14px;top:12px;bottom:12px;border-radius:3px}
.art-ace{left:18px;right:18px;top:26px;bottom:26px;border-radius:50%}
.red .art{background:radial-gradient(circle,#8e1a22 0%,#3a0b0f 70%,var(--card) 100%)}
.silver .art{background:radial-gradient(circle,#8f897c 0%,#3a3833 70%,var(--card) 100%)}
.joker-word{position:absolute;left:5px;top:4px;font-family:"Roboto Slab",serif;font-weight:700;font-size:5px;line-height:1.05;display:flex;flex-direction:column}
.joker-word-b{left:auto;top:auto;right:5px;bottom:4px;transform:rotate(180deg)}
.card-back{background:linear-gradient(160deg,var(--back-blue),var(--back-deep));border-color:#222}
.back-pattern{position:absolute;inset:3px;background:radial-gradient(circle,#3a8ee0 0%,var(--back-blue) 60%,var(--back-deep) 100%);border-radius:2px}
.back-brand{position:absolute;left:0;right:0;top:50%;transform:translateY(-50%);text-align:center;font-family:"Roboto Slab",serif;font-weight:700;font-size:8px;line-height:1.15;color:var(--silver)}
</style>
</head>
<body>
<svg width="0" height="0" style="position:absolute" aria-hidden="true">
  <symbol id="h" viewBox="0 0 20 20"><path d="M10 18C4 13 1 10 1 6A4.5 4.5 0 0 1 10 4A4.5 4.5 0 0 1 19 6C19 10 16 13 10 18Z"/></symbol>
  <symbol id="d" viewBox="0 0 20 20"><path d="M10 1L17 10L10 19L3 10Z"/></symbol>
  <symbol id="s" viewBox="0 0 20 20"><path d="M10 1C6 6 1 9 1 12.5A4 4 0 0 0 8.5 14L7 19H13L11.5 14A4 4 0 0 0 19 12.5C19 9 14 6 10 1Z"/></symbol>
  <symbol id="c" viewBox="0 0 20 20"><circle cx="10" cy="5.5" r="4"/><circle cx="5" cy="11" r="4"/><circle cx="15" cy="11" r="4"/><path d="M9 11L7 19H13L11 11Z"/></symbol>
</svg>

<main class="sheet">

<section class="suit-row row-hearts">
  <div class="card red"><span class="joker-word">J<br>O<br>K<br>E<br>R</span><div class="art" role="img" aria-label="Red jester hat illustration"></div><span class="joker-word joker-word-b">J<br>O<br>K<br>E<br>R</span></div>
  <div class="card red"><span class="idx">A<svg><use href="#h"/></svg></span><div class="art art-ace" role="img" aria-label="Ornate lace heart illustration"></div><span class="idx idx-b">A<svg><use href="#h"/></svg></span></div>
  <div class="card red"><span class="idx">K<svg><use href="#h"/></svg></span><div class="art" role="img" aria-label="King of hearts line illustration"></div><span class="idx idx-b">K<svg><use href="#h"/></svg></span></div>
  <div class="card red"><span class="idx">Q<svg><use href="#h"/></svg></span><div class="art" role="img" aria-label="Queen of hearts line illustration"></div><span class="idx idx-b">Q<svg><use href="#h"/></svg></span></div>
  <div class="card red"><span class="idx">J<svg><use href="#h"/></svg></span><div class="art" role="img" aria-label="Jack of hearts line illustration"></div><span class="idx idx-b">J<svg><use href="#h"/></svg></span></div>
  <div class="card red"><span class="idx">10<svg><use href="#h"/></svg></span>
    <svg class="pip x-l y-a"><use href="#h"/></svg><svg class="pip x-r y-a"><use href="#h"/></svg><svg class="pip x-l y-b"><use href="#h"/></svg><svg class="pip x-r y-b"><use href="#h"/></svg><svg class="pip x-l y-c"><use href="#h"/></svg><svg class="pip x-r y-c"><use href="#h"/></svg><svg class="pip x-l y-d"><use href="#h"/></svg><svg class="pip x-r y-d"><use href="#h"/></svg><svg class="pip x-c y-e"><use href="#h"/></svg><svg class="pip x-c y-f"><use href="#h"/></svg>
    <span class="idx idx-b">10<svg><use href="#h"/></svg></span></div>
  <div class="card red"><span class="idx">9<svg><use href="#h"/></svg></span>
    <svg class="pip x-l y-a"><use href="#h"/></svg><svg class="pip x-r y-a"><use href="#h"/></svg><svg class="pip x-l y-b"><use href="#h"/></svg><svg class="pip x-r y-b"><use href="#h"/></svg><svg class="pip x-c y-m"><use href="#h"/></svg><svg class="pip x-l y-c"><use href="#h"/></svg><svg class="pip x-r y-c"><use href="#h"/></svg><svg class="pip x-l y-d"><use href="#h"/></svg><svg class="pip x-r y-d"><use href="#h"/></svg>
    <span class="idx idx-b">9<svg><use href="#h"/></svg></span></div>
  <div class="card red"><span class="idx">8<svg><use href="#h"/></svg></span>
    <svg class="pip x-l y-a"><use href="#h"/></svg><svg class="pip x-r y-a"><use href="#h"/></svg><svg class="pip x-l y-b"><use href="#h"/></svg><svg class="pip x-r y-b"><use href="#h"/></svg><svg class="pip x-l y-c"><use href="#h"/></svg><svg class="pip x-r y-c"><use href="#h"/></svg><svg class="pip x-l y-d"><use href="#h"/></svg><svg class="pip x-r y-d"><use href="#h"/></svg>
    <span class="idx idx-b">8<svg><use href="#h"/></svg></span></div>
  <div class="card red"><span class="idx">7<svg><use href="#h"/></svg></span>
    <svg class="pip x-l y-a"><use href="#h"/></svg><svg class="pip x-r y-a"><use href="#h"/></svg><svg class="pip x-c y-e"><use href="#h"/></svg><svg class="pip x-l y-m"><use href="#h"/></svg><svg class="pip x-r y-m"><use href="#h"/></svg><svg class="pip x-l y-d"><use href="#h"/></svg><svg class="pip x-r y-d"><use href="#h"/></svg>
    <span class="idx idx-b">7<svg><use href="#h"/></svg></span></div>
  <div class="card red"><span class="idx">6<svg><use href="#h"/></svg></span>
    <svg class="pip x-l y-a"><use href="#h"/></svg><svg class="pip x-r y-a"><use href="#h"/></svg><svg class="pip x-l y-m"><use href="#h"/></svg><svg class="pip x-r y-m"><use href="#h"/></svg><svg class="pip x-l y-d"><use href="#h"/></svg><svg class="pip x-r y-d"><use href="#h"/></svg>
    <span class="idx idx-b">6<svg><use href="#h"/></svg></span></div>
  <div class="card red"><span class="idx">5<svg><use href="#h"/></svg></span>
    <svg class="pip x-l y-a"><use href="#h"/></svg><svg class="pip x-r y-a"><use href="#h"/></svg><svg class="pip x-c y-m"><use href="#h"/></svg><svg class="pip x-l y-d"><use href="#h"/></svg><svg class="pip x-r y-d"><use href="#h"/></svg>
    <span class="idx idx-b">5<svg><use href="#h"/></svg></span></div>
  <div class="card red"><span class="idx">4<svg><use href="#h"/></svg></span>
    <svg class="pip x-l y-a"><use href="#h"/></svg><svg class="pip x-r y-a"><use href="#h"/></svg><svg class="pip x-l y-d"><use href="#h"/></svg><svg class="pip x-r y-d"><use href="#h"/></svg>
    <span class="idx idx-b">4<svg><use href="#h"/></svg></span></div>
  <div class="card red"><span class="idx">3<svg><use href="#h"/></svg></span>
    <svg class="pip x-c y-a"><use href="#h"/></svg><svg class="pip x-c y-m"><use href="#h"/></svg><svg class="pip x-c y-d"><use href="#h"/></svg>
    <span class="idx idx-b">3<svg><use href="#h"/></svg></span></div>
  <div class="card red"><span class="idx">2<svg><use href="#h"/></svg></span>
    <svg class="pip x-c y-a"><use href="#h"/></svg><svg class="pip x-c y-d"><use href="#h"/></svg>
    <span class="idx idx-b">2<svg><use href="#h"/></svg></span></div>
</section>

<section class="suit-row row-spades">
  <div class="card card-back"><div class="back-pattern" role="img" aria-label="Blue ornamental card back pattern"></div><p class="back-brand">Kettleby<br>Twins</p></div>
  <div class="card silver"><span class="idx">A<svg><use href="#s"/></svg></span><div class="art art-ace" role="img" aria-label="Ornate filigree spade illustration"></div><span class="idx idx-b">A<svg><use href="#s"/></svg></span></div>
  <div class="card silver"><span class="idx">K<svg><use href="#s"/></svg></span><div class="art" role="img" aria-label="King of spades line illustration"></div><span class="idx idx-b">K<svg><use href="#s"/></svg></span></div>
  <div class="card silver"><span class="idx">Q<svg><use href="#s"/></svg></span><div class="art" role="img" aria-label="Queen of spades line illustration"></div><span class="idx idx-b">Q<svg><use href="#s"/></svg></span></div>
  <div class="card silver"><span class="idx">J<svg><use href="#s"/></svg></span><div class="art" role="img" aria-label="Jack of spades line illustration"></div><span class="idx idx-b">J<svg><use href="#s"/></svg></span></div>
  <div class="card silver"><span class="idx">10<svg><use href="#s"/></svg></span>
    <svg class="pip x-l y-a"><use href="#s"/></svg><svg class="pip x-r y-a"><use href="#s"/></svg><svg class="pip x-l y-b"><use href="#s"/></svg><svg class="pip x-r y-b"><use href="#s"/></svg><svg class="pip x-l y-c"><use href="#s"/></svg><svg class="pip x-r y-c"><use href="#s"/></svg><svg class="pip x-l y-d"><use href="#s"/></svg><svg class="pip x-r y-d"><use href="#s"/></svg><svg class="pip x-c y-e"><use href="#s"/></svg><svg class="pip x-c y-f"><use href="#s"/></svg>
    <span class="idx idx-b">10<svg><use href="#s"/></svg></span></div>
  <div class="card silver"><span class="idx">9<svg><use href="#s"/></svg></span>
    <svg class="pip x-l y-a"><use href="#s"/></svg><svg class="pip x-r y-a"><use href="#s"/></svg><svg class="pip x-l y-b"><use href="#s"/></svg><svg class="pip x-r y-b"><use href="#s"/></svg><svg class="pip x-c y-m"><use href="#s"/></svg><svg class="pip x-l y-c"><use href="#s"/></svg><svg class="pip x-r y-c"><use href="#s"/></svg><svg class="pip x-l y-d"><use href="#s"/></svg><svg class="pip x-r y-d"><use href="#s"/></svg>
    <span class="idx idx-b">9<svg><use href="#s"/></svg></span></div>
  <div class="card silver"><span class="idx">8<svg><use href="#s"/></svg></span>
    <svg class="pip x-l y-a"><use href="#s"/></svg><svg class="pip x-r y-a"><use href="#s"/></svg><svg class="pip x-l y-b"><use href="#s"/></svg><svg class="pip x-r y-b"><use href="#s"/></svg><svg class="pip x-l y-c"><use href="#s"/></svg><svg class="pip x-r y-c"><use href="#s"/></svg><svg class="pip x-l y-d"><use href="#s"/></svg><svg class="pip x-r y-d"><use href="#s"/></svg>
    <span class="idx idx-b">8<svg><use href="#s"/></svg></span></div>
  <div class="card silver"><span class="idx">7<svg><use href="#s"/></svg></span>
    <svg class="pip x-l y-a"><use href="#s"/></svg><svg class="pip x-r y-a"><use href="#s"/></svg><svg class="pip x-c y-e"><use href="#s"/></svg><svg class="pip x-l y-m"><use href="#s"/></svg><svg class="pip x-r y-m"><use href="#s"/></svg><svg class="pip x-l y-d"><use href="#s"/></svg><svg class="pip x-r y-d"><use href="#s"/></svg>
    <span class="idx idx-b">7<svg><use href="#s"/></svg></span></div>
  <div class="card silver"><span class="idx">6<svg><use href="#s"/></svg></span>
    <svg class="pip x-l y-a"><use href="#s"/></svg><svg class="pip x-r y-a"><use href="#s"/></svg><svg class="pip x-l y-m"><use href="#s"/></svg><svg class="pip x-r y-m"><use href="#s"/></svg><svg class="pip x-l y-d"><use href="#s"/></svg><svg class="pip x-r y-d"><use href="#s"/></svg>
    <span class="idx idx-b">6<svg><use href="#s"/></svg></span></div>
  <div class="card silver"><span class="idx">5<svg><use href="#s"/></svg></span>
    <svg class="pip x-l y-a"><use href="#s"/></svg><svg class="pip x-r y-a"><use href="#s"/></svg><svg class="pip x-c y-m"><use href="#s"/></svg><svg class="pip x-l y-d"><use href="#s"/></svg><svg class="pip x-r y-d"><use href="#s"/></svg>
    <span class="idx idx-b">5<svg><use href="#s"/></svg></span></div>
  <div class="card silver"><span class="idx">4<svg><use href="#s"/></svg></span>
    <svg class="pip x-l y-a"><use href="#s"/></svg><svg class="pip x-r y-a"><use href="#s"/></svg><svg class="pip x-l y-d"><use href="#s"/></svg><svg class="pip x-r y-d"><use href="#s"/></svg>
    <span class="idx idx-b">4<svg><use href="#s"/></svg></span></div>
  <div class="card silver"><span class="idx">3<svg><use href="#s"/></svg></span>
    <svg class="pip x-c y-a"><use href="#s"/></svg><svg class="pip x-c y-m"><use href="#s"/></svg><svg class="pip x-c y-d"><use href="#s"/></svg>
    <span class="idx idx-b">3<svg><use href="#s"/></svg></span></div>
  <div class="card silver"><span class="idx">2<svg><use href="#s"/></svg></span>
    <svg class="pip x-c y-a"><use href="#s"/></svg><svg class="pip x-c y-d"><use href="#s"/></svg>
    <span class="idx idx-b">2<svg><use href="#s"/></svg></span></div>
</section>

<section class="suit-row row-diamonds">
  <div class="card card-back"><div class="back-pattern" role="img" aria-label="Blue ornamental card back pattern"></div><p class="back-brand">Kettleby<br>Twins</p></div>
  <div class="card red"><span class="idx">A<svg><use href="#d"/></svg></span><div class="art art-ace" role="img" aria-label="Ornate filigree diamond illustration"></div><span class="idx idx-b">A<svg><use href="#d"/></svg></span></div>
  <div class="card red"><span class="idx">K<svg><use href="#d"/></svg></span><div class="art" role="img" aria-label="King of diamonds line illustration"></div><span class="idx idx-b">K<svg><use href="#d"/></svg></span></div>
  <div class="card red"><span class="idx">Q<svg><use href="#d"/></svg></span><div class="art" role="img" aria-label="Queen of diamonds line illustration"></div><span class="idx idx-b">Q<svg><use href="#d"/></svg></span></div>
  <div class="card red"><span class="idx">J<svg><use href="#d"/></svg></span><div class="art" role="img" aria-label="Jack of diamonds line illustration"></div><span class="idx idx-b">J<svg><use href="#d"/></svg></span></div>
  <div class="card red"><span class="idx">10<svg><use href="#d"/></svg></span>
    <svg class="pip x-l y-a"><use href="#d"/></svg><svg class="pip x-r y-a"><use href="#d"/></svg><svg class="pip x-l y-b"><use href="#d"/></svg><svg class="pip x-r y-b"><use href="#d"/></svg><svg class="pip x-l y-c"><use href="#d"/></svg><svg class="pip x-r y-c"><use href="#d"/></svg><svg class="pip x-l y-d"><use href="#d"/></svg><svg class="pip x-r y-d"><use href="#d"/></svg><svg class="pip x-c y-e"><use href="#d"/></svg><svg class="pip x-c y-f"><use href="#d"/></svg>
    <span class="idx idx-b">10<svg><use href="#d"/></svg></span></div>
  <div class="card red"><span class="idx">9<svg><use href="#d"/></svg></span>
    <svg class="pip x-l y-a"><use href="#d"/></svg><svg class="pip x-r y-a"><use href="#d"/></svg><svg class="pip x-l y-b"><use href="#d"/></svg><svg class="pip x-r y-b"><use href="#d"/></svg><svg class="pip x-c y-m"><use href="#d"/></svg><svg class="pip x-l y-c"><use href="#d"/></svg><svg class="pip x-r y-c"><use href="#d"/></svg><svg class="pip x-l y-d"><use href="#d"/></svg><svg class="pip x-r y-d"><use href="#d"/></svg>
    <span class="idx idx-b">9<svg><use href="#d"/></svg></span></div>
  <div class="card red"><span class="idx">8<svg><use href="#d"/></svg></span>
    <svg class="pip x-l y-a"><use href="#d"/></svg><svg class="pip x-r y-a"><use href="#d"/></svg><svg class="pip x-l y-b"><use href="#d"/></svg><svg class="pip x-r y-b"><use href="#d"/></svg><svg class="pip x-l y-c"><use href="#d"/></svg><svg class="pip x-r y-c"><use href="#d"/></svg><svg class="pip x-l y-d"><use href="#d"/></svg><svg class="pip x-r y-d"><use href="#d"/></svg>
    <span class="idx idx-b">8<svg><use href="#d"/></svg></span></div>
  <div class="card red"><span class="idx">7<svg><use href="#d"/></svg></span>
    <svg class="pip x-l y-a"><use href="#d"/></svg><svg class="pip x-r y-a"><use href="#d"/></svg><svg class="pip x-c y-e"><use href="#d"/></svg><svg class="pip x-l y-m"><use href="#d"/></svg><svg class="pip x-r y-m"><use href="#d"/></svg><svg class="pip x-l y-d"><use href="#d"/></svg><svg class="pip x-r y-d"><use href="#d"/></svg>
    <span class="idx idx-b">7<svg><use href="#d"/></svg></span></div>
  <div class="card red"><span class="idx">6<svg><use href="#d"/></svg></span>
    <svg class="pip x-l y-a"><use href="#d"/></svg><svg class="pip x-r y-a"><use href="#d"/></svg><svg class="pip x-l y-m"><use href="#d"/></svg><svg class="pip x-r y-m"><use href="#d"/></svg><svg class="pip x-l y-d"><use href="#d"/></svg><svg class="pip x-r y-d"><use href="#d"/></svg>
    <span class="idx idx-b">6<svg><use href="#d"/></svg></span></div>
  <div class="card red"><span class="idx">5<svg><use href="#d"/></svg></span>
    <svg class="pip x-l y-a"><use href="#d"/></svg><svg class="pip x-r y-a"><use href="#d"/></svg><svg class="pip x-c y-m"><use href="#d"/></svg><svg class="pip x-l y-d"><use href="#d"/></svg><svg class="pip x-r y-d"><use href="#d"/></svg>
    <span class="idx idx-b">5<svg><use href="#d"/></svg></span></div>
  <div class="card red"><span class="idx">4<svg><use href="#d"/></svg></span>
    <svg class="pip x-l y-a"><use href="#d"/></svg><svg class="pip x-r y-a"><use href="#d"/></svg><svg class="pip x-l y-d"><use href="#d"/></svg><svg class="pip x-r y-d"><use href="#d"/></svg>
    <span class="idx idx-b">4<svg><use href="#d"/></svg></span></div>
  <div class="card red"><span class="idx">3<svg><use href="#d"/></svg></span>
    <svg class="pip x-c y-a"><use href="#d"/></svg><svg class="pip x-c y-m"><use href="#d"/></svg><svg class="pip x-c y-d"><use href="#d"/></svg>
    <span class="idx idx-b">3<svg><use href="#d"/></svg></span></div>
  <div class="card red"><span class="idx">2<svg><use href="#d"/></svg></span>
    <svg class="pip x-c y-a"><use href="#d"/></svg><svg class="pip x-c y-d"><use href="#d"/></svg>
    <span class="idx idx-b">2<svg><use href="#d"/></svg></span></div>
</section>

<section class="suit-row row-clubs">
  <div class="card silver"><span class="joker-word">J<br>O<br>K<br>E<br>R</span><div class="art" role="img" aria-label="Silver jester hat illustration"></div><span class="joker-word joker-word-b">J<br>O<br>K<br>E<br>R</span></div>
  <div class="card silver"><span class="idx">A<svg><use href="#c"/></svg></span><div class="art art-ace" role="img" aria-label="Ornate filigree club illustration"></div><span class="idx idx-b">A<svg><use href="#c"/></svg></span></div>
  <div class="card silver"><span class="idx">K<svg><use href="#c"/></svg></span><div class="art" role="img" aria-label="King of clubs line illustration"></div><span class="idx idx-b">K<svg><use href="#c"/></svg></span></div>
  <div class="card silver"><span class="idx">Q<svg><use href="#c"/></svg></span><div class="art" role="img" aria-label="Queen of clubs line illustration"></div><span class="idx idx-b">Q<svg><use href="#c"/></svg></span></div>
  <div class="card silver"><span class="idx">J<svg><use href="#c"/></svg></span><div class="art" role="img" aria-label="Jack of clubs line illustration"></div><span class="idx idx-b">J<svg><use href="#c"/></svg></span></div>
  <div class="card silver"><span class="idx">10<svg><use href="#c"/></svg></span>
    <svg class="pip x-l y-a"><use href="#c"/></svg><svg class="pip x-r y-a"><use href="#c"/></svg><svg class="pip x-l y-b"><use href="#c"/></svg><svg class="pip x-r y-b"><use href="#c"/></svg><svg class="pip x-l y-c"><use href="#c"/></svg><svg class="pip x-r y-c"><use href="#c"/></svg><svg class="pip x-l y-d"><use href="#c"/></svg><svg class="pip x-r y-d"><use href="#c"/></svg><svg class="pip x-c y-e"><use href="#c"/></svg><svg class="pip x-c y-f"><use href="#c"/></svg>
    <span class="idx idx-b">10<svg><use href="#c"/></svg></span></div>
  <div class="card silver"><span class="idx">9<svg><use href="#c"/></svg></span>
    <svg class="pip x-l y-a"><use href="#c"/></svg><svg class="pip x-r y-a"><use href="#c"/></svg><svg class="pip x-l y-b"><use href="#c"/></svg><svg class="pip x-r y-b"><use href="#c"/></svg><svg class="pip x-c y-m"><use href="#c"/></svg><svg class="pip x-l y-c"><use href="#c"/></svg><svg class="pip x-r y-c"><use href="#c"/></svg><svg class="pip x-l y-d"><use href="#c"/></svg><svg class="pip x-r y-d"><use href="#c"/></svg>
    <span class="idx idx-b">9<svg><use href="#c"/></svg></span></div>
  <div class="card silver"><span class="idx">8<svg><use href="#c"/></svg></span>
    <svg class="pip x-l y-a"><use href="#c"/></svg><svg class="pip x-r y-a"><use href="#c"/></svg><svg class="pip x-l y-b"><use href="#c"/></svg><svg class="pip x-r y-b"><use href="#c"/></svg><svg class="pip x-l y-c"><use href="#c"/></svg><svg class="pip x-r y-c"><use href="#c"/></svg><svg class="pip x-l y-d"><use href="#c"/></svg><svg class="pip x-r y-d"><use href="#c"/></svg>
    <span class="idx idx-b">8<svg><use href="#c"/></svg></span></div>
  <div class="card silver"><span class="idx">7<svg><use href="#c"/></svg></span>
    <svg class="pip x-l y-a"><use href="#c"/></svg><svg class="pip x-r y-a"><use href="#c"/></svg><svg class="pip x-c y-e"><use href="#c"/></svg><svg class="pip x-l y-m"><use href="#c"/></svg><svg class="pip x-r y-m"><use href="#c"/></svg><svg class="pip x-l y-d"><use href="#c"/></svg><svg class="pip x-r y-d"><use href="#c"/></svg>
    <span class="idx idx-b">7<svg><use href="#c"/></svg></span></div>
  <div class="card silver"><span class="idx">6<svg><use href="#c"/></svg></span>
    <svg class="pip x-l y-a"><use href="#c"/></svg><svg class="pip x-r y-a"><use href="#c"/></svg><svg class="pip x-l y-m"><use href="#c"/></svg><svg class="pip x-r y-m"><use href="#c"/></svg><svg class="pip x-l y-d"><use href="#c"/></svg><svg class="pip x-r y-d"><use href="#c"/></svg>
    <span class="idx idx-b">6<svg><use href="#c"/></svg></span></div>
  <div class="card silver"><span class="idx">5<svg><use href="#c"/></svg></span>
    <svg class="pip x-l y-a"><use href="#c"/></svg><svg class="pip x-r y-a"><use href="#c"/></svg><svg class="pip x-c y-m"><use href="#c"/></svg><svg class="pip x-l y-d"><use href="#c"/></svg><svg class="pip x-r y-d"><use href="#c"/></svg>
    <span class="idx idx-b">5<svg><use href="#c"/></svg></span></div>
  <div class="card silver"><span class="idx">4<svg><use href="#c"/></svg></span>
    <svg class="pip x-l y-a"><use href="#c"/></svg><svg class="pip x-r y-a"><use href="#c"/></svg><svg class="pip x-l y-d"><use href="#c"/></svg><svg class="pip x-r y-d"><use href="#c"/></svg>
    <span class="idx idx-b">4<svg><use href="#c"/></svg></span></div>
  <div class="card silver"><span class="idx">3<svg><use href="#c"/></svg></span>
    <svg class="pip x-c y-a"><use href="#c"/></svg><svg class="pip x-c y-m"><use href="#c"/></svg><svg class="pip x-c y-d"><use href="#c"/></svg>
    <span class="idx idx-b">3<svg><use href="#c"/></svg></span></div>
  <div class="card silver"><span class="idx">2<svg><use href="#c"/></svg></span>
    <svg class="pip x-c y-a"><use href="#c"/></svg><svg class="pip x-c y-d"><use href="#c"/></svg>
    <span class="idx idx-b">2<svg><use href="#c"/></svg></span></div>
</section>

</main>
</body>
</html>
```